Mobile Fitness snd Therapy Business Card Design

I need a business card designed for my mobile fitness and therapy business.

Please view the images that I have uploaded. I like the simplicity of the design that I have attached. I adapted it with my information

Target Market(s)

Those seeking personal training, injury rehabilitation or massage therapy.

Industry/Entity Type

Business

Contact Information for Business Card

Derek Fulham - MSc, CAT(C), RMT, CSCS, Pn2
e-mail: derek@vantrelo.com
website: www.vantrelo.com
instagram: @derek_fulham

Font styles to use
Sans Serif

Colors
3176b5
0355a3

Requirements
Must have
• "Contact us to receive a FREE assessment"
• Services offered:
• Personal Training
• Golf Fitness
• Injury Rehab
• Massage Therapy
• Yoga
Nice to have
• Consistent colours with brand
• - Dark Blue: #232837
• - Blue: #5096f0
• Consistent look/feel with the website: www.vantrelo.com

```html
<!DOCTYPE html>
<html lang="en">
<head>
<meta charset="UTF-8">
<title>Vantrelo Business Card</title>
<link rel="stylesheet" href="https://fonts.googleapis.com/css2?family=Montserrat:wght@700;800&family=Open+Sans:wght@400;600&display=swap">
<style>
  :root {
    --ink-navy: #232837;
    --brand-blue: #3176b5;
    --brand-deep: #0355a3;
    --card-bg: #ffffff;
    --card-edge: #c9ccd2;
    --page-bg: #e6e8eb;
    --text-dark: #1e2230;
  }
  html, body {
    margin: 0;
    padding: 0;
    width: 1200px;
    height: 970px;
    overflow: hidden;
    background: var(--page-bg);
  }
  .business-card {
    position: absolute;
    left: 100px;
    top: 207px;
    width: 1000px;
    height: 556px;
    background: var(--card-bg);
    border: 1px solid var(--card-edge);
    box-sizing: border-box;
    font-family: "Open Sans", Arial, sans-serif;
    color: var(--text-dark);
  }
  .edge-bar {
    position: absolute;
    top: 239px;
    width: 18px;
    height: 196px;
    background: var(--ink-navy);
  }
  .edge-bar--left { left: 0; }
  .edge-bar--right { right: 0; }
  .brand-name {
    position: absolute;
    left: 0;
    right: 0;
    top: 92px;
    text-align: center;
    font-family: "Montserrat", Arial, sans-serif;
    font-weight: 800;
    font-size: 62px;
    letter-spacing: 6px;
    line-height: 1;
    color: var(--ink-navy);
    margin: 0;
  }
  .brand-tagline {
    position: absolute;
    left: 0;
    right: 0;
    top: 148px;
    text-align: center;
    font-family: "Montserrat", Arial, sans-serif;
    font-weight: 800;
    font-size: 21px;
    letter-spacing: 3.4px;
    color: var(--ink-navy);
    margin: 0;
  }
  .contact-column {
    position: absolute;
    left: 119px;
    top: 238px;
  }
  .person-name {
    margin: 0;
    font-family: "Montserrat", Arial, sans-serif;
    font-weight: 800;
    font-size: 29px;
    line-height: 38px;
    color: var(--ink-navy);
  }
  .person-credentials {
    margin: 0 0 22px;
    font-size: 21px;
    line-height: 30px;
    color: var(--brand-blue);
  }
  .contact-list, .service-list {
    list-style: none;
    margin: 0;
    padding: 0;
  }
  .contact-item {
    display: flex;
    align-items: center;
    font-size: 24px;
    line-height: 37px;
    color: var(--text-dark);
  }
  .contact-icon {
    width: 22px;
    height: 22px;
    margin-right: 12px;
    flex: none;
  }
  .column-divider {
    position: absolute;
    left: 500px;
    top: 239px;
    width: 3px;
    height: 196px;
    background: var(--ink-navy);
  }
  .service-column {
    position: absolute;
    left: 572px;
    top: 230px;
  }
  .service-item {
    display: flex;
    align-items: center;
    font-size: 26px;
    line-height: 42.5px;
    color: var(--text-dark);
  }
  .service-marker {
    width: 13px;
    height: 13px;
    margin-right: 13px;
    background: var(--brand-deep);
    flex: none;
  }
  .cta-line {
    position: absolute;
    left: 0;
    right: 0;
    top: 484px;
    text-align: center;
    font-size: 26px;
    margin: 0;
    color: var(--text-dark);
  }
</style>
</head>
<body>
  <section class="business-card">
    <div class="edge-bar edge-bar--left"></div>
    <div class="edge-bar edge-bar--right"></div>

    <h1 class="brand-name">VANTRELO</h1>
    <p class="brand-tagline">NUTRITION - FITNESS - HEALTH</p>

    <div class="contact-column">
      <h2 class="person-name">DEREK FULHAM</h2>
      <p class="person-credentials">MSc, CAT(C), RMT, CSCS, Pn2</p>
      <ul class="contact-list">
        <li class="contact-item">
          <svg class="contact-icon" viewBox="0 0 22 22" aria-hidden="true">
            <rect x="3" y="3" width="16" height="16" fill="var(--ink-navy)"/>
          </svg>
          @derek_fulham
        </li>
        <li class="contact-item">
          <svg class="contact-icon" viewBox="0 0 22 22" aria-hidden="true">
            <rect x="2" y="5" width="18" height="13" fill="var(--ink-navy)"/>
            <polyline points="2,5 11,12 20,5" fill="none" stroke="#ffffff" stroke-width="1.6"/>
          </svg>
          derek@vantrelo.com
        </li>
        <li class="contact-item">
          <svg class="contact-icon" viewBox="0 0 22 22" aria-hidden="true">
            <circle cx="11" cy="11" r="8.5" fill="none" stroke="var(--ink-navy)" stroke-width="2"/>
            <ellipse cx="11" cy="11" rx="3.8" ry="8.5" fill="none" stroke="var(--ink-navy)" stroke-width="1.6"/>
            <line x1="2.5" y1="11" x2="19.5" y2="11" stroke="var(--ink-navy)" stroke-width="1.6"/>
          </svg>
          www.vantrelo.com
        </li>
      </ul>
    </div>

    <div class="column-divider"></div>

    <div class="service-column">
      <ul class="service-list">
        <li class="service-item"><span class="service-marker"></span>Personal Training</li>
        <li class="service-item"><span class="service-marker"></span>Golf Fitness</li>
        <li class="service-item"><span class="service-marker"></span>Injury Rehab</li>
        <li class="service-item"><span class="service-marker"></span>Massage Therapy</li>
        <li class="service-item"><span class="service-marker"></span>Yoga</li>
      </ul>
    </div>

    <p class="cta-line">Contact us to receive a FREE assessment</p>
  </section>
</body>
</html>
```